Construction proffessionals servicing the inner suburbs of Melbournes NorthWest specialising in aler

I would like a web site that is sharp, contemporary and simple to navigate, ie.not too many pages. i would like a home page with some info about us, who we are what our history is and my passion for building and construction based on impeccable customer focus. i would like a projects page and somewhere for clients to add testimonials. i would like a project calculator as well so prospective clients can work out a rough budget prior to contacting. i would like the colours to be in line with my logo which i have uploaded. i have many photos which can be used and can be shared via drop box when required. I would like it to be personal to capture our transparent process. i would like to add our company process as well. be brave and take risks.

Target Market(s)

People renovating and extending their homes, people needing inspections on new homes and pre-purchase inspections

Industry/Entity Type

Construction

Number of Pages Required

5+ page

Requirements
Must have
• Professional, easy to navigate, provide viewers with a happy experience, look great, contacts, project calculator, link through to my training company www.qdmn.learnhub.example also check rowenhq on instagram for pics
Nice to have
• Links to instagram, fonts to match email signature

```html
<!DOCTYPE html>
<html lang="en">
<head>
<meta charset="utf-8">
<title>Rowen Build Group</title>
<link rel="stylesheet" href="https://fonts.googleapis.com/css2?family=Open+Sans:ital,wght@0,400;0,600;0,700;1,400&display=swap">
<style>
:root{
  --orange:#f08a1c;
  --dark:#3a3a3a;
  --footer:#2f2f2f;
  --footer-bottom:#242424;
  --text:#555;
  --muted:#8a8a8a;
  --light:#f2f2f2;
  --line:#dcdcdc;
  --white:#fff;
}
*{box-sizing:border-box;margin:0;padding:0}
html,body{width:1200px;height:2200px;overflow:hidden}
body{font-family:"Open Sans",Arial,sans-serif;color:var(--text);background:var(--white);font-size:13px;line-height:1.6}
.page{width:1200px;height:2200px;position:relative}

.site-header{height:78px;display:flex;justify-content:space-between;align-items:center;padding:0 40px}
.brand{display:flex;align-items:center;gap:10px;font-weight:700;font-size:20px;color:var(--orange)}
.brand-mark{width:34px;height:34px;background:var(--orange)}
.header-right{display:flex;flex-direction:column;align-items:flex-end;gap:10px}
.social{display:flex;gap:5px}
.social span{width:18px;height:18px;background:var(--orange);display:block}
.main-nav{display:flex;gap:26px;font-size:12px;font-weight:600;color:var(--dark)}
.main-nav a{color:inherit;text-decoration:none}
.main-nav a.active{color:var(--orange)}

.hero{position:relative;height:440px;background:linear-gradient(180deg,#b9b2a6 0%,#8d8274 55%,#5f5548 100%)}
.hero-arrow{position:absolute;top:200px;width:36px;height:36px;background:rgba(0,0,0,.35);display:flex;align-items:center;justify-content:center}
.hero-arrow.prev{left:20px}.hero-arrow.next{right:20px}
.hero-dots{position:absolute;bottom:18px;left:0;right:0;display:flex;justify-content:center;gap:8px}
.hero-dots span{width:9px;height:9px;border-radius:50%;background:rgba(255,255,255,.55)}
.hero-dots span.on{background:var(--orange)}

.tagline{height:90px;display:flex;align-items:center;justify-content:center;gap:24px;color:var(--muted);font-style:italic;font-size:17px;text-align:center;border-bottom:1px solid var(--line);margin:0 40px;line-height:1.4}

.welcome{padding:28px 90px 0;text-align:center}
.welcome h1{font-size:24px;font-weight:700;color:var(--dark);margin-bottom:30px}
.questions{display:flex;justify-content:space-between;gap:30px;text-align:left;margin-bottom:28px}
.question{display:flex;gap:10px;flex:1;font-size:14px;color:var(--dark)}
.q-icon{flex:none;width:22px;height:22px;border-radius:50%;background:var(--dark);color:var(--white);font-size:13px;font-weight:700;display:flex;align-items:center;justify-content:center}
.welcome p{font-size:12px;color:var(--muted);margin-bottom:22px}
.btn{display:inline-block;padding:7px 18px;font-size:11px;font-weight:600;color:var(--white);background:var(--dark);text-decoration:none}
.btn.orange{background:var(--orange)}
.btn-row{display:flex;gap:8px;justify-content:center}

.two-col{display:flex;gap:50px;margin:48px 40px 0;padding-top:34px;border-top:1px solid var(--line);height:420px}
.about{flex:1.6}
.calc{flex:1}
.two-col h2{font-size:26px;font-weight:700;color:var(--dark);margin-bottom:6px}
.about h3{font-size:14px;font-weight:600;color:var(--dark);margin-bottom:10px}
.about p,.calc p{font-size:12px;color:var(--muted);margin-bottom:20px}
.right{text-align:right}
.calc-visual{height:130px;background:linear-gradient(135deg,#dfe9f1,#9fb6c8);margin:14px 0 16px}

.testimonials{background:var(--light);height:490px;padding:42px 40px 0;text-align:center}
.testimonials h2{font-size:26px;font-weight:700;color:var(--dark);padding-bottom:14px;border-bottom:1px solid var(--line);margin-bottom:34px}
.testimonial{display:flex;gap:60px;text-align:left;align-items:flex-start}
.avatar{flex:none;width:220px;height:220px;border-radius:50%;background:linear-gradient(180deg,#cfe3ee,#8fb4cc);margin-left:90px}
.quote-head{font-size:16px;color:var(--orange);margin-bottom:2px}
.quote-sub{font-size:20px;font-weight:700;color:var(--dark);margin-bottom:40px}
.quote{font-size:12px;color:var(--muted);font-style:italic}
.t-dots{display:flex;justify-content:center;gap:8px;margin-top:20px}
.t-dots span{width:8px;height:8px;border-radius:50%;background:#ccc}
.t-dots span.on{background:var(--orange)}

.site-footer{background:var(--footer);height:284px;padding:38px 40px 0;display:flex;gap:50px;color:#aaa;font-size:11.5px}
.footer-col{flex:1}
.footer-col h4{color:var(--white);font-size:12px;font-weight:700;margin-bottom:12px;letter-spacing:.5px}
.footer-col ul{list-style:none}
.footer-col li{margin-bottom:4px}
.contact-line{display:flex;gap:8px;align-items:center;margin-bottom:6px}
.field{height:24px;background:#444;margin-bottom:8px;padding:3px 8px;color:#888}
.footer-bottom{background:var(--footer-bottom);height:60px;padding:0 40px;display:flex;justify-content:space-between;align-items:center;color:#888;font-size:11px}
.footer-bottom .social span{background:#666}
</style>
</head>
<body>
<div class="page">

<header class="site-header">
  <div class="brand"><span class="brand-mark"></span>Rowen Build Group</div>
  <div class="header-right">
    <div class="social"><span></span><span></span><span></span><span></span></div>
    <nav class="main-nav">
      <a class="active" href="#">Home</a><a href="#">About Us</a><a href="#">Services</a><a href="#">Blog</a><a href="#">Testimonials</a><a href="#">Project Calculator</a><a href="#">Contact Us</a>
    </nav>
  </div>
</header>

<section class="hero" role="img" aria-label="Photo of two builders smiling in front of a renovated weatherboard house">
  <div class="hero-arrow prev"><svg width="14" height="14" viewBox="0 0 14 14"><path d="M9 2 4 7l5 5" stroke="#fff" stroke-width="2" fill="none"/></svg></div>
  <div class="hero-arrow next"><svg width="14" height="14" viewBox="0 0 14 14"><path d="M5 2l5 5-5 5" stroke="#fff" stroke-width="2" fill="none"/></svg></div>
  <div class="hero-dots"><span class="on"></span><span></span><span></span></div>
</section>

<div class="tagline">PROVIDING QUALITY EXPERT ADVICE, COMMON SENSE AND FRIENDLY PROFES-<br>SIONAL SERVICE</div>

<section class="welcome">
  <h1>Welcome to the Rowen Build Group Pty Ltd website.</h1>
  <div class="questions">
    <div class="question"><span class="q-icon">?</span>How can we help you?</div>
    <div class="question"><span class="q-icon">?</span>Do you have a building issue?</div>
    <div class="question"><span class="q-icon">?</span>Do you need building advice, or simply someone to help you through the battlefield of the building industry?</div>
  </div>
  <p>If you are renovating or extending your home in Melbourne's inner north west, Rowen Build Group is ready to help. We combine trade experience with honest advice so every client understands the process, the costs and the timeline. From pre-purchase inspections to full alterations and additions, our team stays focused on quality workmanship, clear communication and a happy build from the first visit to the final handover.</p>
  <div class="btn-row"><a class="btn" href="#">Read More</a><a class="btn" href="#">View Works</a></div>
</section>

<section class="two-col">
  <div class="about">
    <h2>About Us</h2>
    <h3>The family that is Rowen Build Group Pty Ltd</h3>
    <p>Rowen Build Group started as a small family crew and has grown into a trusted builder across the inner suburbs. Our director brings more than twenty years on the tools and a real passion for building, with every project guided by impeccable customer focus. We keep the process transparent, share each step with our clients and treat every home as if it were our own. Whether it is a renovation, an extension or a new home inspection, we bring the same care.</p>
    <div class="right"><a class="btn" href="#">Read More</a></div>
  </div>
  <div class="calc">
    <h2>Project Calculator</h2>
    <div class="calc-visual" role="img" aria-label="Photo of a calculator on building plans"></div>
    <p>Plan ahead with our simple project calculator. Enter the size and type of your job to see a rough budget before you get in touch with our team.</p>
    <div class="right"><a class="btn orange" href="#">Calculate</a></div>
  </div>
</section>

<section class="testimonials">
  <h2>Testimonials</h2>
  <div class="testimonial">
    <div class="avatar" role="img" aria-label="Illustration of a happy client"></div>
    <div>
      <div class="quote-head">Lorem ipsum dolor sit</div>
      <div class="quote-sub">QUISQUE VOLUTPAT MATTIS EROS</div>
      <p class="quote">From the first meeting the team explained every stage of our extension and kept us updated each week. The work was tidy, on time and on budget, and any questions were answered straight away. We would happily recommend Rowen Build Group to anyone planning a renovation in the inner north west.</p>
    </div>
  </div>
  <div class="t-dots"><span class="on"></span><span></span><span></span></div>
</section>

<footer class="site-footer">
  <div class="footer-col">
    <h4>WHO WE ARE</h4>
    <p>Construction professionals servicing the inner suburbs of Melbourne's north west, specialising in alterations, additions and inspections.</p>
  </div>
  <div class="footer-col">
    <h4>USEFUL LINKS</h4>
    <ul><li>Home</li><li>About Us</li><li>Services</li><li>Blog</li><li>Testimonials</li><li>Contact Us</li></ul>
  </div>
  <div class="footer-col">
    <h4>GET IN TOUCH</h4>
    <p style="margin-bottom:10px">Have a question about your project? Send us a message and we will reply within one business day.</p>
    <div class="contact-line"><svg width="10" height="12" viewBox="0 0 10 12"><path d="M5 0a4 4 0 0 0-4 4c0 3 4 8 4 8s4-5 4-8a4 4 0 0 0-4-4z" fill="#aaa"/></svg>12 Sample St, Northcote VIC 3070</div>
    <div class="contact-line"><svg width="10" height="12" viewBox="0 0 10 12"><rect x="1" y="0" width="8" height="12" rx="1.5" fill="#aaa"/></svg>03 9000 0000</div>
    <div class="contact-line"><svg width="12" height="9" viewBox="0 0 12 9"><rect width="12" height="9" fill="#aaa"/><path d="M0 0l6 5 6-5" stroke="#2f2f2f" fill="none"/></svg>hello@rowenhq.example</div>
  </div>
  <div class="footer-col">
    <h4>CONTACT</h4>
    <p style="margin-bottom:10px">Subscribe for news and project updates from our team.</p>
    <div class="field">Name</div>
    <div class="field">Email</div>
    <a class="btn orange" href="#">Subscribe</a>
  </div>
</footer>
<div class="footer-bottom">
  <span>© 2015 rowenhq. All rights reserved.</span>
  <div class="social"><span></span><span></span><span></span><span></span></div>
</div>

</div>
</body>
</html>
```